Business Card Design For Office Furniture Clearance Company

Kestrel Office Clearance - our company name pretty much explains what we do, we clear offices for high end clients, mainly plc's and large international companies.

We require a nice looking business card that displays professionalism but without being too serious.

It would be nice to see just a little more than a conventional boring business card, make sure you add some flare.

Industry/Entity Type

Office Furniture

Contact Information for Business Card

CARD 1

Mark Holloway
Director
mark@kestrelofficeclearance.co.uk
m: 07700 153928

t: 01632 960418
www.kestrelofficeclearance.co.uk

Kestrel Office Clearance
Unit K4 B
2-8 Fenwick Lane
Hartwell
Northbridge
ZZ9 4QT

Tidy office clearances… done fast and done right, always.

CARD 2

Peter Radford
Director
peter@kestrelofficeclearance.co.uk
m: 07700 382615

t: 01632 960418

Kestrel Office Clearance
Unit K4 B
2-8 Fenwick Lane
Hartwell
Northbridge
ZZ9 4QT

Font styles to use
Sans Serif

Requirements
Must have
• A white background - as we have a blue logo.
Nice to have
• Nice use of the logo - play around with this and dissect it.

```html
<!DOCTYPE html>
<html lang="en">
<head>
<meta charset="utf-8">
<title>Kestrel Office Clearance — Business Cards</title>
<link rel="stylesheet" href="https://fonts.googleapis.com/css2?family=Source+Sans+3:ital,wght@0,400;0,600;1,400&display=swap">
<style>
  :root {
    --backdrop: #8e8f90;
    --card: #f4f4f5;
    --brand-blue: #1f6cab;
    --ink: #3f3f42;
    --band-dark: #3a3a3d;
    --rule: #c9c9cc;
  }
  * { box-sizing: border-box; margin: 0; padding: 0; }
  html, body {
    width: 1105px;
    height: 1200px;
    overflow: hidden;
    background: var(--backdrop);
    font-family: "Source Sans 3", "Myriad Pro", Arial, sans-serif;
    color: var(--ink);
  }
  .card {
    position: absolute;
    left: 182px;
    width: 746px;
    height: 427px;
    background: var(--card);
    overflow: hidden;
  }
  .card--front { top: 119px; }
  .card--back { top: 635px; }

  .brand-block {
    position: absolute;
    left: 30px;
    top: 70px;
    width: 290px;
    text-align: center;
  }
  .brand-mark {
    display: block;
    margin: 0 auto 18px;
    width: 120px;
    height: 120px;
    border-radius: 50%;
    background: var(--brand-blue);
  }
  .brand-name {
    font-size: 27px;
    font-weight: 600;
    line-height: 1.15;
    color: var(--brand-blue);
  }

  .divider {
    position: absolute;
    left: 336px;
    top: 75px;
    width: 1px;
    height: 283px;
    background: var(--rule);
  }

  .details {
    position: absolute;
    left: 367px;
    top: 72px;
    font-size: 20px;
    line-height: 27px;
  }
  .details__name {
    font-size: 28px;
    line-height: 34px;
    color: var(--brand-blue);
  }
  .details__role { margin-bottom: 8px; }
  .details__company { color: var(--brand-blue); font-weight: 600; }
  .contact-list {
    list-style: none;
    margin-top: 14px;
  }
  .contact-list li {
    display: flex;
    align-items: center;
    height: 28.5px;
  }
  .contact-list svg {
    width: 18px;
    height: 18px;
    margin-left: 6px;
    margin-right: 12px;
    fill: var(--brand-blue);
    flex: none;
  }

  .footer-band {
    position: absolute;
    left: 0;
    bottom: 0;
    width: 746px;
    height: 28px;
  }

  .back-brand {
    position: absolute;
    left: 0;
    right: 0;
    top: 100px;
    display: flex;
    align-items: center;
    justify-content: center;
    gap: 22px;
  }
  .back-brand .brand-mark { margin: 0; width: 140px; height: 140px; }
  .back-brand .brand-name { font-size: 34px; text-align: left; }
  .tagline {
    position: absolute;
    left: 0;
    right: 0;
    top: 346px;
    text-align: center;
    font-style: italic;
    font-size: 20px;
    color: var(--ink);
  }
</style>
</head>
<body>

<section class="card card--front" aria-label="Business card front">
  <div class="brand-block">
    <span class="brand-mark"></span>
    <div class="brand-name">Kestrel Office<br>Clearance</div>
  </div>

  <div class="divider"></div>

  <div class="details">
    <div class="details__name">Mark Holloway</div>
    <div class="details__role">Director</div>
    <div class="details__company">Kestrel Office Clearance</div>
    <div>Unit K4 B, 2-8 Fenwick Lane</div>
    <div>Hartwell, Northbridge, ZZ9 4QT</div>

    <ul class="contact-list">
      <li>
        <svg viewBox="0 0 24 24" aria-hidden="true"><path d="M6.6 10.8a15.2 15.2 0 0 0 6.6 6.6l2.2-2.2a1 1 0 0 1 1-.25 11.4 11.4 0 0 0 3.6.57 1 1 0 0 1 1 1V20a1 1 0 0 1-1 1A17 17 0 0 1 3 4a1 1 0 0 1 1-1h3.5a1 1 0 0 1 1 1c0 1.25.2 2.45.57 3.57a1 1 0 0 1-.25 1z"/></svg>
        01632 960418
      </li>
      <li>
        <svg viewBox="0 0 24 24" aria-hidden="true"><path d="M7 1h10a2 2 0 0 1 2 2v18a2 2 0 0 1-2 2H7a2 2 0 0 1-2-2V3a2 2 0 0 1 2-2zm0 3v14h10V4zm5 15.5a1.2 1.2 0 1 0 0 2.4 1.2 1.2 0 0 0 0-2.4z"/></svg>
        07700 153928
      </li>
      <li>
        <svg viewBox="0 0 24 24" aria-hidden="true"><path d="M2 5h20v14H2zm2 2v.5l8 5 8-5V7zm0 2.8V17h16V9.8l-8 5z"/></svg>
        mark@kestrelofficeclearance.co.uk
      </li>
      <li>
        <svg viewBox="0 0 24 24" aria-hidden="true"><path d="M12 2a10 10 0 1 0 0 20 10 10 0 0 0 0-20zm6.9 6h-3a15.6 15.6 0 0 0-1.4-3.6A8 8 0 0 1 18.9 8zM12 4c.8 1.2 1.5 2.5 1.9 4h-3.8c.4-1.5 1.1-2.8 1.9-4zM4.3 14a8.2 8.2 0 0 1 0-4h3.4a16 16 0 0 0 0 4zm.8 2h3a15.6 15.6 0 0 0 1.4 3.6A8 8 0 0 1 5.1 16zm3-8h-3a8 8 0 0 1 4.4-3.6A15.6 15.6 0 0 0 8.1 8zM12 20c-.8-1.2-1.5-2.5-1.9-4h3.8c-.4 1.5-1.1 2.8-1.900 4zm2.3-6H9.7a14.7 14.7 0 0 1 0-4h4.6a14.7 14.7 0 0 1 0 4zm.2 5.6a15.6 15.6 0 0 0 1.4-3.6h3a8 8 0 0 1-4.4 3.6zm1.8-5.6a16 16 0 0 0 0-4h3.4a8.2 8.2 0 0 1 0 4z"/></svg>
        www.kestrelofficeclearance.co.uk
      </li>
    </ul>
  </div>

  <svg class="footer-band" viewBox="0 0 746 28" aria-hidden="true">
    <polygon points="0,0 493,0 485,28 0,28" fill="var(--brand-blue)"/>
    <polygon points="498,0 746,0 746,28 490,28" fill="var(--band-dark)"/>
  </svg>
</section>

<section class="card card--back" aria-label="Business card back">
  <div class="back-brand">
    <span class="brand-mark"></span>
    <div class="brand-name">Kestrel Office<br>Clearance</div>
  </div>
  <p class="tagline">Tidy office clearances… done fast and done right, always.</p>
</section>

</body>
</html>
```